Webdesign für Kleingruppenreisen in die Südsteiermark
Zielgruppe
Wir sind ein Start-Up Unternehmen, das als Kleingruppenreisen in die Südsteiermark veranstaltet; der Schwerpunkt liegt auf dem Kulinarischen. Zielgruppe sind Geschäftsleute, die diese Kurzreisen (Do-So) für Marketingzwecke oder als Mitarbeiterbonus (oder auch privat) nutzen möchten.
Aufgabenstellung
Die Homepage soll eine Online-Shop Möglichkeit bieten, in der die Reise (bisher gibt es nur einen Ablauf) gebucht werden kann. Optisch sollte sie sich an das bereits von Ihnen erstellte Logo anlehnen und möglichst ansprechende Fotos von der Südsteiermark, Graz, Leoben usw. enthalten. (Siehe die beiden Flyer und das Logo)
Wir haben inzwischen Bildfreigaben von Haldauer und dem Tourismusverband Kellwinden erhalten und können auch eigene Bilder zur Verfügung stellen. Bitte kontaktieren Sie uns dafür, wenn nötig.

```html
<!DOCTYPE html>
<html lang="de">
<head>
<meta charset="utf-8">
<title>Tafelweg Reisen – Kulinarische Kleingruppenreisen</title>
<link href="https://fonts.googleapis.com/css2?family=Lato:wght@300;400;700;900&family=Kaushan+Script&display=swap" rel="stylesheet">
<style>
:root{
  --green:#5cc045;
  --green-dark:#3f9a2c;
  --yellow:#fde03a;
  --orange:#f15a24;
  --ink:#333;
  --black:#0d0d0d;
  --white:#fff;
}
*{box-sizing:border-box;margin:0;padding:0}
html,body{width:1200px;height:3307px;overflow:hidden}
body{position:relative;font-family:'Lato',sans-serif;color:var(--ink);background:var(--white)}
.abs{position:absolute}
.script{font-family:'Kaushan Script',cursive}
.btn{position:absolute;display:flex;align-items:center;justify-content:center;font-size:25px;color:var(--ink);white-space:nowrap}
.btn-yellow{background:var(--yellow)}
.btn-orange{background:var(--orange);color:var(--white)}
.brand{position:absolute;display:flex;align-items:center;gap:8px;background:var(--white);font-weight:900;color:var(--orange);white-space:nowrap}
.brand .dot{width:14px;height:14px;border-radius:50%;background:var(--green);flex:none}

/* header */
.account{left:893px;top:0;width:220px;height:40px;background:#1a1a1a;display:flex;align-items:center;justify-content:center;gap:16px;font-size:22px;font-weight:700;color:var(--white)}
.account .up{color:var(--yellow)}
.nav{left:555px;top:50px;display:flex;font-size:15px;color:#222;white-space:nowrap}
.nav a{display:block;padding:10px 15px;text-decoration:none;color:inherit}
.nav a.active{background:var(--yellow)}

/* hero */
.hero{left:0;top:90px;width:1200px;height:475px;background:var(--green)}
.hero-photo{left:0;top:90px;width:1200px;height:475px;background:linear-gradient(160deg,#b8cfe0 0%,#d6e3ea 20%,#7fb04a 45%,#4f8a2a 75%,#3c6e22 100%);clip-path:polygon(685px 0,1200px 0,1200px 475px,500px 475px)}
.hero-explore{left:80px;top:140px;font-size:80px;color:var(--white)}
.hero-big{left:80px;font-size:70px;font-weight:300;color:var(--white);letter-spacing:1px;white-space:nowrap}
.hero-tag{left:84px;top:421px;font-size:28px;font-weight:700;color:#1c1c1c;white-space:nowrap}
.dots{left:591px;top:524px;display:flex;gap:8px}
.dots i{width:14px;height:14px;border-radius:50%;background:var(--white)}
.dots i:first-child{background:var(--yellow)}

/* museum */
.museum-photo{left:87px;top:732px;width:461px;height:334px;background:linear-gradient(90deg,#e8e4dc,#b46a34 45%,#8a4a22 70%,#d9d2c6);box-shadow:0 12px 18px rgba(0,0,0,.25);overflow:hidden}
.ribbon{position:absolute;right:-48px;top:34px;width:200px;height:34px;background:#c71fd1;color:var(--white);transform:rotate(45deg);font-size:14px;font-weight:900;display:flex;align-items:center;justify-content:center;letter-spacing:1px;white-space:nowrap}
.museum-title{right:88px;top:730px;font-size:36px;color:#333;white-space:nowrap}
.museum-title b{color:var(--orange)}
.museum-rule{left:1050px;top:787px;width:62px;height:4px;background:var(--orange)}
.museum-text{right:88px;top:812px;font-size:20px;line-height:35.5px;text-align:right;font-weight:300;color:#333;white-space:nowrap}

/* inspired */
.inspired{left:0;top:1118px;width:1200px;height:425px;background:var(--green);clip-path:polygon(0 0,1200px 12px,1200px 425px,0 415px)}
.inspired-title{left:0;top:1150px;width:1200px;text-align:center;font-size:60px;color:var(--white)}
.video{left:306px;top:1242px;width:584px;height:326px;background:radial-gradient(circle at 45% 50%,#f2eed9,#c9b46a 45%,#9a8e3e 80%)}
.video-bar{left:306px;top:1531px;width:584px;height:37px;background:#2d2d2d;display:flex;align-items:center;gap:10px;padding:0 12px;font-size:11px;color:var(--white);white-space:nowrap}
.video-bar .track{flex:1;height:6px;background:#111;border-radius:3px}

/* features */
.feature{position:absolute;top:1608px;width:210px}
.feature .ico{width:50px;height:50px;background:var(--green);border-radius:4px}
.feature h3{position:absolute;left:67px;top:6px;font-size:15px;font-weight:400;color:#555;line-height:19px;white-space:nowrap}
.feature p{margin-top:23px;font-size:12.5px;line-height:27px;text-align:justify;font-weight:300;color:#444}

/* packages */
.pk-title{left:0;top:1842px;width:1200px;text-align:center;font-size:32px;color:#333}
.pk-title b{color:var(--yellow);font-weight:700}
.pk-rule{left:548px;top:1890px;width:104px;height:4px;background:#333}
.pk-box{left:86px;top:1913px;width:1024px;height:444px;border:2px solid #333}
.pk-bg{left:100px;top:1926px;width:990px;height:418px;background:linear-gradient(90deg,#c7d2a2 0%,#e9ead8 35%,#f5efdf 60%,#e9dcc0 100%);overflow:hidden}
.pk-bg .ribbon{background:#22c234;right:-44px;top:30px}
.pk-bar{left:269px;top:1948px;width:651px;height:46px;background:var(--orange);color:var(--white);font-size:33px;font-weight:900;display:flex;align-items:center;justify-content:center;white-space:nowrap}
.pk-photo{left:126px;top:2019px;width:414px;height:313px;background:linear-gradient(160deg,#5f8d33,#8a6b45 55%,#3a2e32)}
.arrows{left:1001px;top:2024px;display:flex;gap:14px}
.arrows span{width:25px;height:25px;border-radius:50%;background:#111;display:flex;align-items:center;justify-content:center}
.pk-head{right:134px;top:2068px;font-size:26px;font-weight:900;text-align:right;line-height:31px;color:#1c1c1c;white-space:nowrap}
.pk-line{left:978px;top:2150px;width:88px;height:4px;background:#1c1c1c}
.pk-text{right:134px;top:2176px;font-size:17.5px;line-height:25px;text-align:right;color:#222;white-space:nowrap}

/* why */
.why{left:0;top:2372px;width:1200px;height:545px;background:var(--green)}
.tabs{left:87px;top:2428px;width:493px;height:67px;background:#eee;display:flex;font-size:20px;color:#222;white-space:nowrap}
.tabs div{display:flex;align-items:center;justify-content:center}
.tabs .t1{width:175px;background:var(--white);border-bottom:4px solid var(--orange)}
.tabs .t2{width:116px}
.tabs .t3{width:202px}
.why-text{left:87px;top:2522px;width:491px;font-size:17px;line-height:31.2px;text-align:justify;color:var(--white);font-weight:300}
.devices{left:612px;top:2390px;width:588px;height:440px;background:linear-gradient(135deg,rgba(255,255,255,.05),rgba(40,40,40,.35) 50%,rgba(255,255,255,.2));border-radius:6px}

/* footer */
.foot-line{left:0;top:2913px;width:1200px;height:6px;background:var(--yellow)}
.footer{left:0;top:2919px;width:1200px;height:343px;background:var(--black)}
.f-h{position:absolute;top:2945px;font-size:20px;font-weight:700;color:var(--green);white-space:nowrap}
.f-links{position:absolute;top:2993px;font-size:13.5px;color:var(--white);line-height:35.5px;list-style:none;white-space:nowrap}
.f-links .on{font-size:15px}
.f-contact{position:absolute;left:444px;font-size:12px;color:var(--white);display:flex;gap:18px;line-height:26px;white-space:nowrap}
.field{position:absolute;left:834px;width:278px;background:var(--white);font-size:15px;color:#888;padding:8px 18px}
.submit{left:834px;top:3179px;width:141px;height:41px;background:var(--yellow);font-size:19px;color:#222;display:flex;align-items:center;justify-content:center}
.bottom{left:0;top:3262px;width:1200px;height:45px;background:#1f1f1f;color:var(--white);font-size:12px;display:flex;align-items:center;justify-content:center}
</style>
</head>
<body>

<!-- header -->
<div class="abs account"><span class="up">Sign Up</span><span>I</span><span>Log In</span></div>
<nav class="abs nav">
  <a class="active" href="#">HOME</a><a href="#">SERVICES</a><a href="#">ONLINE SHOP</a><a href="#">BLOG</a><a href="#">LEGAL</a><a href="#">CONTACT</a>
</nav>

<!-- hero -->
<div class="abs hero"></div>
<div class="abs hero-photo" role="img" aria-label="Hügelige Weinberglandschaft der Südsteiermark mit Bauernhäusern"></div>
<div class="brand" style="left:87px;top:25px;width:185px;height:96px;justify-content:center;font-size:22px;box-shadow:0 0 0 1px #eee"><span class="dot"></span>Tafelweg Reisen</div>
<div class="abs hero-explore script">Explore</div>
<div class="abs hero-big" style="top:238px">DREAM</div>
<div class="abs hero-big" style="top:330px">DESTINATION</div>
<div class="abs hero-tag">YOUR DREAM COMES TRUE HERE</div>
<div class="btn btn-yellow" style="left:87px;top:477px;width:249px;height:56px">Tour Now</div>
<div class="abs dots"><i></i><i></i><i></i><i></i></div>

<!-- museum -->
<div class="brand" style="left:980px;top:646px;width:130px;height:64px;justify-content:flex-end;font-size:15px"><span class="dot" style="width:10px;height:10px"></span>Tafelweg Reisen</div>
<div class="abs museum-photo" role="img" aria-label="Ausstellungshalle des Brauereimuseums mit Holzfassade"><div class="ribbon">SPECIAL OFFER</div></div>
<div class="abs museum-title">LARGEST <b>HALDAUER MUSEUM</b></div>
<div class="abs museum-rule"></div>
<p class="abs museum-text">Lorem Ipsum is simply dummy text of the printing and<br>typesetting industry. Lorem Ipsum has been the indus-<br>try's standard dummy text ever since the 1500s<br>Lorem Ipsum is simply dummy text of the printing and<br>typesetting industry. Lorem Ipsum has been the indus-</p>
<div class="btn btn-yellow" style="left:609px;top:1011px;width:243px;height:55px">Sign Up</div>
<div class="btn btn-orange" style="left:869px;top:1011px;width:243px;height:55px">Shop Now</div>

<!-- inspired -->
<div class="abs inspired"></div>
<div class="abs inspired-title script">Get Inspired</div>
<div class="abs video" role="img" aria-label="Video-Standbild: Weinglas vor herbstlichem Weinberg"></div>
<svg class="abs" style="left:512px;top:1306px" width="162" height="162" viewBox="0 0 162 162" aria-hidden="true">
  <circle cx="81" cy="81" r="74" fill="#fff" stroke="#000" stroke-width="12"/>
  <polygon points="62,50 62,112 112,81" fill="#000"/>
</svg>
<div class="abs video-bar"><span>▶</span><div class="track"></div><span>00:00 / <span style="color:#e33">00:00</span></span><span>◀</span><span style="width:40px;height:4px;background:#555"></span><span>⛶</span></div>

<!-- features -->
<div class="feature" style="left:87px"><div class="ico"></div><h3>Special<br>Activities</h3><p>Lorem Ipsum is simply dummy text of the printing and typesetting industry. Lorem Ipsum has been the industry's standard dummy text ever since the 1500s</p></div>
<div class="feature" style="left:356px"><div class="ico"></div><h3>Travel<br>Arrangements</h3><p>Lorem Ipsum is simply dummy text of the printing and typesetting industry. Lorem Ipsum has been the industry's standard dummy text ever since the 1500s</p></div>
<div class="feature" style="left:631px"><div class="ico"></div><h3>Private<br>Guide</h3><p>Lorem Ipsum is simply dummy text of the printing and typesetting industry. Lorem Ipsum has been the industry's standard dummy text ever since the 1500s</p></div>
<div class="feature" style="left:904px"><div class="ico"></div><h3>Location<br>Manager</h3><p>Lorem Ipsum is simply dummy text of the printing and typesetting industry. Lorem Ipsum has been the industry's standard dummy text ever since the 1500s</p></div>

<!-- packages -->
<div class="abs pk-title">BEST HOLIDAY <b>PACKAGES</b></div>
<div class="abs pk-rule"></div>
<div class="abs pk-box"></div>
<div class="abs pk-bg" role="img" aria-label="Heller Hintergrund mit Weinglas und Nüssen"><div class="ribbon">SPECIAL OFFER</div></div>
<div class="abs pk-bar">KELLWINDEN TOURISMUS _ INA VOLT</div>
<div class="abs pk-photo" role="img" aria-label="Weinglas mit Trauben und Walnüssen auf einem Holztisch im Garten"></div>
<div class="abs arrows"><span><svg width="10" height="12"><path d="M8 1 2 6l6 5" stroke="#fde03a" stroke-width="2.5" fill="none"/></svg></span><span><svg width="10" height="12"><path d="M2 1l6 5-6 5" stroke="#fde03a" stroke-width="2.5" fill="none"/></svg></span></div>
<div class="abs pk-head">WINTER STAY FOR SINGLE COUPLE @<br>$250.00 FOR 2 NIGHTS</div>
<div class="abs pk-line"></div>
<p class="abs pk-text">Lorem Ipsum is simply dummy text of the printing and typeset-<br>ting industry. Lorem Ipsum has been the industry's standard<br>dummy text ever since the 1500s, when an unknown printer</p>
<div class="btn btn-yellow" style="left:850px;top:2283px;width:214px;height:48px;font-size:23px">Book Now</div>

<!-- why -->
<div class="abs why"></div>
<div class="abs tabs"><div class="t1">Why Best ?</div><div class="t2">Features</div><div class="t3">Store the Goods</div></div>
<p class="abs why-text">Lorem Ipsum is simply dummy text of the printing and typesetting industry. Lorem Ipsum has been the industry's standard dummy text ever since the 1500s. Lorem Ipsum is simply dummy text of the printing and typesetting industry. Lorem Ipsum has been the industry's standard dummy text ever since the 1500s. Lorem Ipsum is simply dummy text of the printing and typesetting industry. Lorem Ipsum has been the industry's standard dummy text ever since the 1500s. Lorem Ipsum is simply dummy text of the printing and typesetting industry. Lorem Ipsum has been the industry's standard dummy text ever since the 1500s.</p>
<div class="abs devices" role="img" aria-label="Website auf Desktop, Laptop, Tablet und Smartphone"></div>

<!-- footer -->
<div class="abs foot-line"></div>
<div class="abs footer"></div>
<div class="f-h" style="left:112px">MENU</div>
<ul class="f-links" style="left:113px"><li>HOME</li><li>SERVICES</li><li class="on">ONLINE SHOP</li><li>BLOG</li><li>LEGAL</li><li>CONTACT</li></ul>
<ul class="f-links" style="left:251px"><li>TERMS &amp; CONDITION</li><li>PRIVACY POLICY</li><li>SITEMAP</li></ul>
<div class="brand" style="left:252px;top:3144px;width:145px;height:76px;justify-content:center;font-size:15px"><span class="dot" style="width:10px;height:10px"></span>Tafelweg Reisen</div>

<div class="f-h" style="left:478px">CONTACT &nbsp;US</div>
<div class="f-contact" style="top:2990px"><svg width="18" height="26" viewBox="0 0 18 26"><path d="M9 1a8 8 0 0 0-8 8c0 6 8 16 8 16s8-10 8-16a8 8 0 0 0-8-8z" fill="#fff"/><circle cx="9" cy="9" r="3" fill="#0d0d0d"/></svg><span>Lorem Ipsum is simply dummy text of the<br>printing and typesetting industry</span></div>
<div class="f-contact" style="top:3059px"><svg width="20" height="14" viewBox="0 0 20 14" style="margin-top:6px"><rect x="1" y="1" width="18" height="12" fill="none" stroke="#fff" stroke-width="1.5"/><path d="M1 1l9 7 9-7" fill="none" stroke="#fff" stroke-width="1.5"/></svg><span>info@tafelweg-mail.de</span></div>
<div class="f-contact" style="top:3106px"><svg width="24" height="24" viewBox="0 0 24 24"><path d="M5 2l4 4-2 3c1 3 4 6 7 7l3-2 4 4-3 4C9 21 3 15 2 5z" fill="#fff"/></svg><span>000-777-9999</span></div>

<div class="f-h" style="left:830px">GET &amp; TOUCH WITH US</div>
<div class="field" style="top:2988px;height:35px">Name</div>
<div class="field" style="top:3035px;height:35px">Email id</div>
<div class="field" style="top:3082px;height:85px">Comments</div>
<div class="abs submit">SUBMIT</div>

<div class="abs bottom">copyright@ www.tafelwegreisen.de</div>
</body>
</html>
```